Mandala Postcard Design

I am in need of a postcard to hand out at a Psychic Fair. I envision the card to having half-of-a Mandala (from my Facebook folder), touched up a bit to make it vibrant and bold. Others vendors will have cards w/photographic backgrounds doing yoga. I'd like mine to stand out for it's line-drawn "cartoonish" nature, solid-color nature. The wording would be my basic contact info and a short description ... something like: "Experience the Magic of Mandala Making ... Next Class will be held: (open space for writing, no lines) The art is contained in this Facebook folder. Lots to choose from, with my favorites being the stronger outlined designs.

https://www.examplesocial.net/Brightorbs/media_set?set=a.20462926615637197.2184852941.783542196&type=3
Updates

I just uploaded a few new drawings that might work better, since they are more round. I want to minimize the white space, for instance, avoid having the left & right corners empty. Another idea could be to use 1/4 mandalas in the corners. I'm ready to make a decision. I want it to look great, but as I gain drawing experience, I'll need to update my cards. Thanks! I'm not sure if this the place for this comment, but I'll also be needing a DVD label for my tutorials, and a front page design for a mandala coloring book.

Target Market(s)

Primarily women interested in metaphysical, psychic, meditation, reiki and a basic interest in art.

Font styles to use
Serif
Sans Serif

Requirements
Should not have
• Should not be on a dark card, really should be a plain white background, it seems, in order to stand out.

```html
<!DOCTYPE html>
<html lang="en">
<head>
<meta charset="utf-8">
<title>Experience the Magic of Mandala Making</title>
<link rel="stylesheet" href="https://fonts.googleapis.com/css2?family=Arimo:wght@400&display=swap">
<style>
  :root {
    --paper: #ffffff;
    --ink: #1a1a1a;
    --navy: #1f2a4a;
    --teal: #3fc1b5;
    --coral: #f0727a;
    --magenta: #b0237a;
    --gold: #f2d02b;
    --lilac: #c9a6d8;
  }
  html, body {
    margin: 0;
    padding: 0;
    width: 1200px;
    height: 929px;
    overflow: hidden;
    background: var(--paper);
  }
  .postcard {
    position: relative;
    width: 1200px;
    height: 929px;
    background: var(--paper);
    font-family: "Arimo", Arial, sans-serif;
    color: var(--ink);
  }
  .art {
    position: absolute;
    display: block;
  }
  .art--top-left { left: 0; top: 0; }
  .art--top-right { right: 0; top: 0; }
  .art--bottom-left { left: 0; bottom: 0; }
  .art--bottom-right { right: 0; bottom: 0; }
  .art--feature { left: 57px; top: 146px; }
  .headline {
    position: absolute;
    left: 600px;
    top: 222px;
    width: 460px;
    margin: 0;
    text-align: center;
    font-weight: 400;
    font-size: 39px;
    line-height: 1.7;
    letter-spacing: -0.8px;
    transform: scaleX(0.93);
    transform-origin: center;
  }
  .next-class {
    position: absolute;
    left: 649px;
    top: 530px;
    margin: 0;
    font-size: 17px;
    letter-spacing: -0.2px;
  }
</style>
</head>
<body>
<main class="postcard">

  <svg class="art art--top-left" width="240" height="260" viewBox="0 0 240 260" role="img" aria-label="Quarter mandala illustration with pink, teal and yellow petals">
    <defs>
      <radialGradient id="tlTone" cx="0" cy="0" r="1">
        <stop offset="0" stop-color="#f0727a"/>
        <stop offset="0.55" stop-color="#3fc1b5"/>
        <stop offset="1" stop-color="#f2d02b"/>
      </radialGradient>
    </defs>
    <path d="M0 0 H225 A225 245 0 0 1 0 255 Z" fill="url(#tlTone)" opacity="0.85"/>
  </svg>

  <svg class="art art--top-right" width="310" height="230" viewBox="0 0 310 230" role="img" aria-label="Quarter mandala line drawing in black with yellow, lilac and magenta accents">
    <defs>
      <radialGradient id="trTone" cx="1" cy="0" r="1">
        <stop offset="0" stop-color="#c9a6d8"/>
        <stop offset="0.6" stop-color="#f2d02b"/>
        <stop offset="1" stop-color="#ffffff"/>
      </radialGradient>
    </defs>
    <path d="M310 0 V225 A305 225 0 0 1 5 0 Z" fill="url(#trTone)" opacity="0.8"/>
  </svg>

  <svg class="art art--feature" width="466" height="466" viewBox="0 0 466 466" role="img" aria-label="Round mandala illustration with a navy spiked border, coral ring and teal centre with coloured figures">
    <defs>
      <radialGradient id="featureTone" cx="0.5" cy="0.5" r="0.5">
        <stop offset="0" stop-color="#b0237a"/>
        <stop offset="0.45" stop-color="#3fc1b5"/>
        <stop offset="0.72" stop-color="#f0727a"/>
        <stop offset="0.8" stop-color="#1f2a4a"/>
        <stop offset="1" stop-color="#1f2a4a"/>
      </radialGradient>
    </defs>
    <circle cx="233" cy="233" r="232" fill="url(#featureTone)"/>
  </svg>

  <svg class="art art--bottom-left" width="240" height="250" viewBox="0 0 240 250" role="img" aria-label="Quarter mandala illustration with pink petals, teal leaves and a yellow centre">
    <defs>
      <radialGradient id="blTone" cx="0" cy="1" r="1">
        <stop offset="0" stop-color="#f2d02b"/>
        <stop offset="0.45" stop-color="#f0727a"/>
        <stop offset="1" stop-color="#3fc1b5"/>
      </radialGradient>
    </defs>
    <path d="M0 250 V10 A235 240 0 0 1 235 250 Z" fill="url(#blTone)" opacity="0.85"/>
  </svg>

  <svg class="art art--bottom-right" width="420" height="400" viewBox="0 0 420 400" role="img" aria-label="Quarter mandala line drawing in black with yellow stars and magenta accents">
    <defs>
      <radialGradient id="brTone" cx="1" cy="1" r="1">
        <stop offset="0" stop-color="#b0237a"/>
        <stop offset="0.5" stop-color="#f2d02b"/>
        <stop offset="1" stop-color="#ffffff"/>
      </radialGradient>
    </defs>
    <path d="M420 400 H5 A415 395 0 0 1 420 5 Z" fill="url(#brTone)" opacity="0.6"/>
  </svg>

  <h1 class="headline">Experience the Magic of<br>Mandala Making</h1>
  <p class="next-class">Next Class will be held :</p>

</main>
</body>
</html>
```